Business Cards for a law firm

Business cards for our law firm. Use our silhoette logo and OAK PARTNERS - check our website (www.oakpartners.example)

Contact Information for Business Card

our silhouette logo, OAK PARTNERS, 800-555-0147, Dorian Pemberton, dorian@oakpartners.example

Requirements
Must have
• our silhouette logo, OAK PARTNERS, 800-555-0147, Dorian Pemberton, dorian@oakpartners.example

```html
<!DOCTYPE html>
<html lang="en">
<head>
<meta charset="utf-8">
<title>Oak Partners – Business Cards</title>
<link rel="stylesheet" href="https://fonts.googleapis.com/css2?family=Lexend+Exa:wght@400&family=Roboto:wght@300;400;700&display=swap">
<style>
  :root {
    --navy: #233166;
    --paper: #ffffff;
    --backdrop: #e3e7e8;
  }
  * { margin: 0; padding: 0; box-sizing: border-box; }
  html, body { width: 1200px; height: 960px; overflow: hidden; }
  body { background: var(--backdrop); position: relative; font-family: "Roboto", sans-serif; color: var(--navy); }

  .card {
    position: absolute;
    left: 250px;
    width: 702px;
    height: 401px;
    background: var(--paper);
    border-radius: 33px;
    overflow: hidden;
  }
  .card--front { top: 60px; }
  .card--back { top: 500px; }
  .card__band {
    position: absolute; left: 0; right: 0; bottom: 0;
    height: 24px; background: var(--navy);
  }

  .brand { position: absolute; display: flex; align-items: center; color: var(--navy); }
  .brand__mark { background: var(--navy); flex: none; }
  .brand__name { font-family: "Lexend Exa", sans-serif; font-weight: 400; line-height: 1; white-space: nowrap; }

  .card--front .brand { left: 112px; top: 170px; gap: 18px; }
  .card--front .brand__mark { width: 58px; height: 58px; }
  .card--front .brand__name { font-size: 36px; }

  .card--back .brand { left: 25px; top: 166px; gap: 14px; }
  .card--back .brand__mark { width: 54px; height: 54px; }
  .card--back .brand__name { font-size: 28px; line-height: 1.02; }

  .divider {
    position: absolute; left: 351px; top: 96px;
    width: 1.5px; height: 212px; background: var(--navy);
  }

  .contact { position: absolute; left: 406px; top: 128px; }
  .contact__name { font-size: 29px; letter-spacing: 0.5px; line-height: 1; white-space: nowrap; margin-bottom: 22px; }
  .contact__first { font-weight: 700; }
  .contact__last { font-weight: 300; }
  .contact__list { list-style: none; }
  .contact__item { display: flex; align-items: center; height: 22px; font-size: 17.5px; letter-spacing: 0.4px; }
  .contact__icon { width: 16px; height: 16px; margin-right: 11px; fill: var(--navy); flex: none; }
</style>
</head>
<body>
  <section class="card card--front">
    <div class="brand">
      <span class="brand__mark"></span>
      <span class="brand__name">OAK PARTNERS</span>
    </div>
    <div class="card__band"></div>
  </section>

  <section class="card card--back">
    <div class="brand">
      <span class="brand__mark"></span>
      <span class="brand__name">OAK<br>PARTNERS</span>
    </div>
    <div class="divider"></div>
    <div class="contact">
      <p class="contact__name"><span class="contact__first">DORIAN</span> <span class="contact__last">PEMBERTON</span></p>
      <ul class="contact__list">
        <li class="contact__item">
          <svg class="contact__icon" viewBox="0 0 24 24" aria-hidden="true"><path d="M6.6 10.8a15.1 15.1 0 0 0 6.6 6.6l2.2-2.2c.3-.3.7-.4 1-.2 1.1.4 2.3.6 3.6.6.6 0 1 .4 1 1V20c0 .6-.4 1-1 1A17 17 0 0 1 3 4c0-.6.4-1 1-1h3.5c.6 0 1 .4 1 1 0 1.3.2 2.5.6 3.6.1.3 0 .7-.2 1z"/></svg>
          800-555-0147
        </li>
        <li class="contact__item">
          <svg class="contact__icon" viewBox="0 0 24 24" aria-hidden="true"><path d="M12 2a10 10 0 1 0 0 20 10 10 0 0 0 0-20zm-1 17.9A8 8 0 0 1 4 12l1-.1L9 16v1a2 2 0 0 0 2 2zm6.9-2.5A2 2 0 0 0 16 16h-1v-3a1 1 0 0 0-1-1H8v-2h2a1 1 0 0 0 1-1V7h2a2 2 0 0 0 2-2v-.4a8 8 0 0 1 2.9 12.8z"/></svg>
          www.oakpartners.example
        </li>
        <li class="contact__item">
          <svg class="contact__icon" viewBox="0 0 24 24" aria-hidden="true"><path d="M3 6h18a1 1 0 0 1 1 1v11a1 1 0 0 1-1 1H3a1 1 0 0 1-1-1V7a1 1 0 0 1 1-1zm1 2.2V17h16V8.2l-8 5.3z"/></svg>
          dorian@oakpartners.example
        </li>
      </ul>
    </div>
    <div class="card__band"></div>
  </section>
</body>
</html>
```